VFX Company Business Card Design Project

The Kestrel Works is a decentralized Visual Effects Studio servicing the television and feature film industries.
Project Brief:
Take our logo that was previously designed on Pencil Harbor and make a double sided business card.
Requirements:
- Card MUST be double sided.
- Front of card MUST have the yellow part of our logo against the dark grey background.
- Back of card is completely up to the designer.
- Back of card must include the complete company logo.
Please follow these File Preparation guidelines:
http://printnook.ca/infopage?file=filetype_en&s=PrintNook_new&lang=en
Business

```html
<!DOCTYPE html>
<html lang="en">
<head>
<meta charset="utf-8">
<title>The Kestrel Works — Business Card</title>
<link rel="stylesheet" href="https://fonts.googleapis.com/css2?family=Questrial&family=Source+Sans+3:wght@400;600&display=swap">
<style>
  :root {
    --backdrop: #d4ad86;
    --card: #2b2b2b;
    --card-edge: #1f1f1f;
    --brand-yellow: #fec52e;
    --slate: #5e6a6d;
    --slate-text: #6f7c7f;
    --cream: #eef3e2;
    --ink-light: #f2f2f2;
    --label-ink: #111111;
  }
  * { margin: 0; padding: 0; box-sizing: border-box; }
  html, body { width: 1200px; height: 788px; overflow: hidden; }
  body {
    position: relative;
    background: var(--backdrop);
    font-family: "Questrial", "Century Gothic", sans-serif;
  }
  .side-label {
    position: absolute;
    font-family: "Source Sans 3", Arial, sans-serif;
    font-size: 22px;
    color: var(--label-ink);
    transform: translateX(-50%);
    white-space: nowrap;
  }
  .label-back { left: 600px; top: 32px; }
  .label-front-1 { left: 327px; top: 403px; }
  .label-front-2 { left: 900px; top: 403px; }

  .card {
    position: absolute;
    width: 524px;
    height: 299px;
    background: var(--card);
    border-radius: 22px;
    overflow: hidden;
    box-shadow: 0 3px 8px rgba(0,0,0,0.35);
  }
  .card-back { left: 338px; top: 78px; }
  .card-front-1 { left: 54px; top: 446px; }
  .card-front-2 { left: 622px; top: 446px; }

  /* Back */
  .back-wordmark {
    position: absolute;
    left: 18px; top: 62px;
    width: 262px;
    font-size: 28px;
    line-height: 1;
    color: var(--slate-text);
    letter-spacing: 0.5px;
    white-space: nowrap;
  }
  .divider {
    position: absolute;
    left: 296px; top: 58px;
    width: 1px; height: 110px;
    background: #555;
  }
  .contact {
    position: absolute;
    left: 322px; top: 54px;
    color: var(--ink-light);
    font-size: 13.5px;
    line-height: 19.5px;
  }
  .contact .person-name { font-size: 20px; line-height: 24px; }
  .contact .designation { color: #cfcfcf; font-size: 13.5px; letter-spacing: 0.8px; margin-bottom: 2px; }
  .contact .key { font-family: "Source Sans 3", Arial, sans-serif; font-weight: 600; font-style: italic; }
  .wave { position: absolute; left: 0; top: 0; }
  .address {
    position: absolute;
    left: 32px; top: 252px;
    color: var(--ink-light);
    font-size: 13px;
    line-height: 18px;
  }

  /* Fronts */
  .front-mark {
    position: absolute;
    display: flex;
    align-items: center;
    gap: 14px;
    white-space: nowrap;
  }
  .front-mark .dot {
    display: block;
    border-radius: 50%;
    background: var(--brand-yellow);
  }
  .card-front-1 .front-mark {
    left: 50%; top: 108px;
    transform: translateX(-50%);
    color: var(--brand-yellow);
    font-size: 40px;
  }
  .card-front-1 .dot { width: 44px; height: 44px; }
  .card-front-2 .front-mark {
    left: 52px; top: 126px;
    color: var(--slate-text);
    font-size: 36px;
  }
  .card-front-2 .dot { width: 46px; height: 46px; }
  .site {
    position: absolute;
    left: 0; right: 0; top: 256px;
    text-align: center;
    color: var(--ink-light);
    font-size: 20px;
    letter-spacing: 3.4px;
  }
</style>
</head>
<body>
  <div class="side-label label-back">Back</div>
  <div class="side-label label-front-1">Front - 1</div>
  <div class="side-label label-front-2">Front - 2</div>

  <section class="card card-back">
    <svg class="wave" width="524" height="299" viewBox="0 0 524 299" aria-hidden="true">
      <path d="M0 238 C 120 222, 260 262, 380 246 C 440 238, 490 222, 524 214 L524 299 L0 299 Z" fill="var(--slate)"/>
      <path d="M112 214 C 220 214, 300 258, 400 244 C 450 237, 495 222, 524 215" fill="none" stroke="#141414" stroke-width="6"/>
      <path d="M110 212 C 220 210, 300 250, 400 238 C 450 232, 495 218, 524 210" fill="none" stroke="var(--cream)" stroke-width="5"/>
    </svg>
    <div class="back-wordmark">The Kestrel Works</div>
    <div class="divider"></div>
    <div class="contact">
      <div class="person-name">Your Name</div>
      <div class="designation">Designation</div>
      <div><span class="key">phone</span> 123-456-7890</div>
      <div><span class="key">cell</span> 123-456-7890</div>
      <div><span class="key">email</span> info@website.com</div>
      <div><span class="key">web</span> www.website.com</div>
    </div>
    <div class="address">0000#, Area Name<br>State Name, Country code</div>
  </section>

  <section class="card card-front-1">
    <div class="front-mark"><span class="dot"></span>The Kestrel Works</div>
    <div class="site">www.website.com</div>
  </section>

  <section class="card card-front-2">
    <div class="front-mark"><span class="dot"></span>The Kestrel Works</div>
    <div class="site">www.website.com</div>
  </section>
</body>
</html>
```